Website visual upgrade

I am seeking expressions of interest for the updating the visuals of my website www.kelvastaffing.net
I am basically seeking a simple,bold and visually strong graphic makeover.using existing or shortly to be modified text.

```html
<!DOCTYPE html>
<html lang="en">
<head>
<meta charset="utf-8">
<title>Kelva Staffing</title>
<link href="https://fonts.googleapis.com/css2?family=Oswald:wght@400;500&family=Open+Sans:wght@400;600;700&family=Cinzel:wght@400&display=swap" rel="stylesheet">
<style>
:root{
  --red:#d2132e;
  --red-dark:#a80e22;
  --ink:#1c1c1c;
  --bar:#1f1f1f;
  --card:#333333;
  --paper:#f3f3f3;
  --grey:#6b6b6b;
  --white:#ffffff;
}
*{margin:0;padding:0;box-sizing:border-box}
html,body{width:1026px;height:1200px;overflow:hidden;background:var(--paper);font-family:"Open Sans",Arial,sans-serif}
.page{position:relative;width:1026px;height:1200px;background:radial-gradient(ellipse at 50% 55%,#fbfbfb 0%,#ececec 100%)}
.abs{position:absolute}

/* top bar */
.topbar{left:0;top:0;width:1026px;height:30px;background:var(--bar)}
.toptab{top:0;height:30px;line-height:30px;font-family:"Oswald",sans-serif;font-size:11px;color:#fff;text-transform:uppercase;text-align:center}
.toptab.active{left:162px;width:64px;background:#151515}
.field{top:8px;height:16px;width:104px;background:#111;border:1px solid #3a3a3a;font-size:6px;color:#888;padding:4px 6px}
.btn-top{top:7px;height:17px;width:79px;background:linear-gradient(#fff,#cfcfcf);font-family:"Oswald",sans-serif;font-size:10px;line-height:17px;text-align:center;color:#222}

/* header */
.header{left:0;top:30px;width:1026px;height:90px;background:linear-gradient(#fafafa,#e4e4e4)}
.brand{font-size:21px;font-weight:700;color:var(--red);letter-spacing:.2px}
.brand-dot{width:14px;height:14px;border-radius:50%;background:var(--ink)}
.nav{top:69px;font-family:"Oswald",sans-serif;font-size:10px;color:#fff;text-transform:uppercase;white-space:nowrap}
.nav-sep{top:60px;width:1px;height:30px;background:rgba(255,255,255,.45)}

/* hero */
.hero{left:0;top:120px;width:1026px;height:251px;background:linear-gradient(180deg,#3a1d24 0%,#8e3f2e 30%,#d1782f 48%,#5a2a3a 62%,#251628 70%,#7b3f6e 84%,#4a2a4a 100%)}
.hero-caption{left:397px;top:215px;width:463px;height:69px;background:rgba(20,20,20,.55)}
.hero-line1{left:428px;top:230px;font-weight:700;font-size:14.5px;color:var(--red);text-transform:uppercase;letter-spacing:-.3px;-webkit-text-stroke:.4px #fff}
.hero-line2{left:437px;top:251px;font-size:11.5px;color:#fff;text-transform:uppercase;letter-spacing:-.2px}
.dot{top:353px;width:5px;height:5px;border-radius:50%;background:rgba(255,255,255,.55)}

/* seeker band */
.seeker{left:0;top:371px;width:1026px;height:74px;background:linear-gradient(#fdfdfd,#e9e9e9);box-shadow:0 3px 5px rgba(0,0,0,.12)}
.seeker-title{left:380px;top:380px;font-family:"Cinzel",serif;font-size:33px;color:#222}
.seeker-sub{left:510px;top:412px;font-size:12.5px;color:#333}
.btn-red{background:var(--red);color:#fff;font-family:"Oswald",sans-serif;text-align:center}

/* cards */
.card{top:481px;width:226px;height:284px;background:var(--card);box-shadow:0 1px 3px rgba(0,0,0,.4)}
.card-head{position:absolute;left:11px;top:0;width:204px;height:31px;background:linear-gradient(#fafafa,#dedede)}
.card-head h2{position:absolute;left:8px;top:6px;font-family:"Oswald",sans-serif;font-weight:500;font-size:14px;color:#444}
.card-icon{position:absolute;right:0;top:0;width:56px;height:31px}
.card-lead{position:absolute;left:18px;top:39px;width:200px;font-size:10.5px;line-height:14px;font-weight:600;color:#fff}
.card-photo{position:absolute;left:11px;top:76px;width:204px;height:86px}
.card-text{position:absolute;left:11px;top:171px;width:204px;font-family:Arial,sans-serif;font-size:8.5px;line-height:18px;color:#eee;text-align:justify}
.read-more{position:absolute;left:11px;top:250px;width:66px;height:20px;background:#fff;border-right:3px solid var(--red);font-size:8px;line-height:20px;color:#222;padding-left:8px}

/* testimonials */
.testi{left:162px;top:796px;width:702px;height:234px;background:#efefef}
.testi-title{left:392px;top:818px;font-weight:700;font-size:25px;color:#222;letter-spacing:-.5px}
.testi-sub{left:486px;top:844px;font-size:10.5px;color:#333}
.avatar-ring{left:238px;top:866px;width:70px;height:70px;border-radius:50%;background:#fff;box-shadow:0 1px 4px rgba(0,0,0,.35)}
.avatar{left:244px;top:872px;width:58px;height:58px;border-radius:50%;background:linear-gradient(#c9d3de,#6c7888)}
.quote{left:318px;top:882px;width:480px;font-size:9.5px;line-height:18px;color:#333}
.name-bar{left:385px;top:977px;width:256px;height:25px;line-height:25px;font-size:10px;color:#fff;text-align:center;background:var(--red)}

/* footer */
.footer{left:0;top:1060px;width:1026px;height:140px;background:#1e1e1e}
.foot-link{font-size:8px;color:#ddd;white-space:nowrap}
.copy{left:173px;top:1187px;font-size:7.5px;color:#ccc}
</style>
</head>
<body>
<div class="page">

  <!-- top bar -->
  <div class="abs topbar"></div>
  <div class="abs toptab active">Client</div>
  <div class="abs toptab" style="left:236px;width:50px">Job Seeker</div>
  <div class="abs field" style="left:469px">Name :</div>
  <div class="abs field" style="left:580px">Email :</div>
  <div class="abs btn-top" style="left:690px">LOGIN</div>
  <div class="abs btn-top" style="left:773px">SIGNUP</div>

  <!-- header -->
  <div class="abs header"></div>
  <svg class="abs" style="left:0;top:30px" width="1026" height="90"><polygon points="385,0 1026,0 1026,90 351,90" fill="#d2132e"/></svg>
  <div class="abs brand-dot" style="left:173px;top:67px"></div>
  <div class="abs brand" style="left:193px;top:58px">Kelva Staffing</div>

  <svg class="abs" style="left:406px;top:68px" width="12" height="11"><path d="M6 0 L12 5.5 L10 5.5 L10 11 L7.5 11 L7.5 7.5 L4.5 7.5 L4.5 11 L2 11 L2 5.5 L0 5.5Z" fill="#fff"/></svg>
  <div class="abs nav" style="left:426px">Home</div>
  <div class="abs nav-sep" style="left:463px"></div>
  <div class="abs nav" style="left:480px">Migration Assistance</div>
  <div class="abs nav-sep" style="left:577px"></div>
  <div class="abs nav" style="left:594px">Job Seeker</div>
  <div class="abs nav-sep" style="left:650px"></div>
  <div class="abs nav" style="left:668px">Useful Links</div>
  <div class="abs nav-sep" style="left:730px"></div>
  <div class="abs nav" style="left:747px">Support</div>
  <div class="abs nav-sep" style="left:795px"></div>
  <div class="abs nav" style="left:812px">Contact Us</div>

  <!-- hero -->
  <div class="abs hero" role="img" aria-label="City skyline silhouette at sunset over water"></div>
  <div class="abs hero-caption"></div>
  <svg class="abs" style="left:397px;top:215px" width="40" height="69"><polygon points="6,0 14,0 34,69 28,69" fill="#d2132e"/></svg>
  <div class="abs hero-line1">We are executive search and selection specialists</div>
  <div class="abs hero-line2">We work exclusively with our clients</div>
  <div class="abs dot" style="left:497px"></div>
  <div class="abs dot" style="left:504px;background:#fff"></div>
  <div class="abs dot" style="left:511px"></div>
  <div class="abs dot" style="left:518px"></div>
  <div class="abs dot" style="left:525px"></div>

  <!-- job seeker band -->
  <div class="abs seeker"></div>
  <svg class="abs" style="left:500px;top:444px" width="26" height="16"><polygon points="0,0 26,0 13,14" fill="#e9e9e9"/></svg>
  <svg class="abs" style="left:346px;top:385px" width="28" height="32"><path d="M2 6 L18 2 L24 8 L24 30 L2 30Z" fill="#fff" stroke="#bbb"/><path d="M8 24 L20 10" stroke="#999" stroke-width="2"/></svg>
  <div class="abs seeker-title">FOR JOB'S SEEKER</div>
  <div class="abs seeker-sub">click here to get the form</div>
  <div class="abs btn-red" style="left:703px;top:395px;width:94px;height:25px;line-height:25px;font-size:11px">CLICK HERE</div>

  <!-- cards -->
  <div class="abs card" style="left:162px">
    <div class="card-head"><h2>WHO WE ARE</h2>
      <svg class="card-icon" viewBox="0 0 56 31"><polygon points="0,0 56,0 56,31 10,31" fill="#d2132e"/><circle cx="30" cy="11" r="4" fill="#fff"/><path d="M23 24 Q23 16 30 16 Q37 16 37 24Z" fill="#fff"/><circle cx="40" cy="11" r="4" fill="#fff"/><path d="M34 24 Q34 16 40 16 Q47 16 47 24Z" fill="#fff"/></svg></div>
    <div class="card-lead">We have recruited for over 400 leading companies.</div>
    <div class="card-photo" role="img" aria-label="Photo of a smiling business team in suits" style="background:linear-gradient(#eaeaea,#7a7a7a)"></div>
    <div class="card-text">There are many variations of passages of Lorem Ipsum available, but the majority have alteration in some form, by injected humour, or randomised words text. All the Lorem Ipsum generators.</div>
    <div class="read-more"><b>+</b> Read more</div>
  </div>
  <div class="abs card" style="left:401px">
    <div class="card-head"><h2>WHAT WE DO</h2>
      <svg class="card-icon" viewBox="0 0 56 31"><polygon points="0,0 56,0 56,31 10,31" fill="#d2132e"/><rect x="27" y="6" width="14" height="18" fill="#fff"/><path d="M30 11h8M30 15h8M30 19h6" stroke="#d2132e" stroke-width="1.5"/></svg></div>
    <div class="card-lead">We are a specialist recruiter to the health sector.</div>
    <div class="card-photo" role="img" aria-label="Black and white photo of a group meeting" style="background:linear-gradient(#dcdcdc,#4a4a4a)"></div>
    <div class="card-text">There are many variations of passages of Lorem Ipsum available, but the majority have alteration in some form, by injected humour, or randomised words text. All the Lorem Ipsum generators.</div>
    <div class="read-more"><b>+</b> Read more</div>
  </div>
  <div class="abs card" style="left:639px">
    <div class="card-head"><h2>OUR APPROACH</h2>
      <svg class="card-icon" viewBox="0 0 56 31"><polygon points="0,0 56,0 56,31 10,31" fill="#d2132e"/><path d="M28 6h14M28 25h14M30 6 L40 25M40 6 L30 25" stroke="#fff" stroke-width="2.2" fill="none"/></svg></div>
    <div class="card-lead">Make your business the best it can be</div>
    <div class="card-photo" role="img" aria-label="Blue eye with planets illustration" style="background:linear-gradient(90deg,#1d3a6e,#8fa6cf 60%,#c9d5ea)"></div>
    <div class="card-text">There are many variations of passages of Lorem Ipsum available, but the majority have alteration in some form, by injected humour, or randomised words text. All the Lorem Ipsum generators.</div>
    <div class="read-more"><b>+</b> Read more</div>
  </div>

  <!-- testimonials -->
  <div class="abs testi"></div>
  <svg class="abs" style="left:356px;top:822px" width="30" height="28"><path d="M1 1h28v18H10l-5 7v-7H1Z" fill="#fff" stroke="#bbb"/><circle cx="9" cy="10" r="1.5" fill="#999"/><circle cx="15" cy="10" r="1.5" fill="#999"/><circle cx="21" cy="10" r="1.5" fill="#999"/></svg>
  <div class="abs testi-title">CLIENT TESTIMONIALS</div>
  <div class="abs testi-sub">what our customer say about us</div>
  <div class="abs avatar-ring"></div>
  <div class="abs avatar" role="img" aria-label="Portrait photo of the client"></div>
  <div class="abs quote">“ There are many variations of passages of Lorem Ipsum available, but the majority have alteration in some form, by injected humour, or randomised words text. All the Lorem Ipsum generators.”</div>
  <svg class="abs" style="left:175px;top:900px" width="24" height="28"><polygon points="22,1 22,27 2,14" fill="#fafafa" stroke="#ccc"/></svg>
  <svg class="abs" style="left:829px;top:900px" width="24" height="28"><polygon points="2,1 2,27 22,14" fill="#fafafa" stroke="#ccc"/></svg>
  <div class="abs name-bar">- Sam R. / Northvale Lending</div>

  <!-- footer -->
  <div class="abs footer"></div>
  <svg class="abs" style="left:0;top:1060px" width="1026" height="140"><polygon points="745,0 1026,0 1026,140 585,140" fill="#f1f1f1"/></svg>
  <div class="abs foot-link" style="left:173px;top:1072px">Help&nbsp;&nbsp;&nbsp;&nbsp;&nbsp;I&nbsp;&nbsp;&nbsp;&nbsp;&nbsp;Contact&nbsp;&nbsp;&nbsp;&nbsp;&nbsp;I&nbsp;&nbsp;&nbsp;&nbsp;&nbsp;Fees&nbsp;&nbsp;&nbsp;&nbsp;&nbsp;I&nbsp;&nbsp;&nbsp;&nbsp;&nbsp;About&nbsp;&nbsp;&nbsp;&nbsp;&nbsp;I&nbsp;&nbsp;&nbsp;&nbsp;&nbsp;Blog&nbsp;&nbsp;&nbsp;&nbsp;&nbsp;I&nbsp;&nbsp;&nbsp;&nbsp;&nbsp;Sitemap&nbsp;&nbsp;&nbsp;&nbsp;&nbsp;I&nbsp;&nbsp;&nbsp;&nbsp;&nbsp;Feedback</div>
  <div class="abs foot-link" style="left:173px;top:1118px">Home&nbsp;&nbsp;&nbsp;&nbsp;&nbsp;&nbsp;&nbsp;&nbsp;&nbsp;&nbsp;&nbsp;&nbsp;I&nbsp;&nbsp;&nbsp;&nbsp;&nbsp;&nbsp;&nbsp;&nbsp;&nbsp;&nbsp;&nbsp;Who we are&nbsp;&nbsp;&nbsp;&nbsp;&nbsp;&nbsp;&nbsp;&nbsp;&nbsp;&nbsp;I&nbsp;&nbsp;&nbsp;&nbsp;&nbsp;&nbsp;&nbsp;&nbsp;&nbsp;&nbsp;Our Approach&nbsp;&nbsp;&nbsp;&nbsp;&nbsp;&nbsp;&nbsp;&nbsp;&nbsp;&nbsp;I&nbsp;&nbsp;&nbsp;&nbsp;&nbsp;&nbsp;&nbsp;&nbsp;&nbsp;&nbsp;What we do&nbsp;&nbsp;&nbsp;&nbsp;&nbsp;&nbsp;&nbsp;&nbsp;&nbsp;&nbsp;I&nbsp;&nbsp;&nbsp;&nbsp;&nbsp;&nbsp;&nbsp;&nbsp;&nbsp;&nbsp;Migration Assistance</div>
  <div class="abs foot-link" style="left:173px;top:1137px">Job Seeker&nbsp;&nbsp;&nbsp;&nbsp;&nbsp;&nbsp;&nbsp;&nbsp;&nbsp;I&nbsp;&nbsp;&nbsp;&nbsp;&nbsp;&nbsp;&nbsp;&nbsp;&nbsp;&nbsp;Useful Links&nbsp;&nbsp;&nbsp;&nbsp;&nbsp;&nbsp;&nbsp;&nbsp;&nbsp;&nbsp;I&nbsp;&nbsp;&nbsp;&nbsp;&nbsp;&nbsp;&nbsp;&nbsp;&nbsp;&nbsp;Support&nbsp;&nbsp;&nbsp;&nbsp;&nbsp;&nbsp;&nbsp;&nbsp;&nbsp;&nbsp;I&nbsp;&nbsp;&nbsp;&nbsp;&nbsp;&nbsp;&nbsp;&nbsp;&nbsp;&nbsp;Contact Us</div>
  <div class="abs brand-dot" style="left:686px;top:1138px"></div>
  <div class="abs brand" style="left:706px;top:1129px">Kelva Staffing</div>
  <div class="abs copy">© Copyright 2013 kelvastaffing.net&nbsp; All Rights Reserved</div>

</div>
</body>
</html>
```